Website Design - TallyPorchHelpers.net

PLEASE CHECK WORD DOCUMENT ATTACHED FOR WEBSITE FLOW.

Target Market(s)

REAL ESTATE AGENTS ARE THE TARGET MARKET

Industry/Entity Type

Real Estate

Coding

Coded - Design and coding required

Number of Pages Required

4 page

Colors

Designer to choose colors to be used in the design.

Requirements
Must have
• WE LIKE RED LOGO ATTACHED
Nice to have
• PLEASE CHECK WORD DOCUMENT ATTACHED FOR WEBSITE FLOW.
Should not have

```html
<!DOCTYPE html>
<html lang="en">
<head>
<meta charset="utf-8">
<title>Tally Porch Helpers</title>
<link href="https://fonts.googleapis.com/css2?family=Oswald:wght@400;500;600&family=Open+Sans:wght@400;600;700&display=swap" rel="stylesheet">
<style>
:root{
  --navy:#1f3a78;
  --navy-deep:#14275a;
  --orange:#f26a1b;
  --blue:#2f6fb5;
  --ink:#333;
  --muted:#666;
  --dark:#2a2d33;
  --gray:#ececec;
  --white:#fff;
}
*{box-sizing:border-box;margin:0;padding:0}
html,body{width:1200px;height:4986px;overflow:hidden}
body{font-family:'Open Sans',Arial,sans-serif;color:var(--ink);background:var(--white);position:relative}
section,header,footer{position:relative;width:1200px;overflow:hidden}
.heading{font-family:'Oswald',Arial,sans-serif;font-weight:400;text-transform:uppercase;text-align:center;font-size:30px;letter-spacing:.5px}
.btn{display:inline-block;font-family:'Oswald',Arial,sans-serif;text-transform:uppercase;color:var(--white);background:var(--orange);font-size:16px;padding:14px 26px;border-radius:3px;letter-spacing:.4px}
.btn-blue{background:var(--blue)}

/* header */
.site-header{height:126px}
.brand{position:absolute;left:86px;top:36px;display:flex;align-items:center;gap:12px}
.brand-mark{width:38px;height:38px;background:var(--navy)}
.brand-name{font-family:'Oswald',Arial,sans-serif;font-weight:600;color:var(--navy);font-size:24px;line-height:1;text-transform:uppercase}
.top-call{position:absolute;right:90px;top:30px;font-size:15px;color:var(--ink);display:flex;align-items:center;gap:8px}
.main-nav{position:absolute;right:90px;top:72px;display:flex;gap:48px;font-size:15px}

/* hero */
.hero{height:522px}
.hero-photo{position:absolute;inset:0;background:linear-gradient(180deg,#b7c3cf 0%,#7e8a8e 35%,#4f6b3a 65%,#3b5a2b 100%)}
.hero-copy{position:absolute;right:90px;top:186px;width:520px;color:var(--white);font-size:24px;line-height:1.4;text-align:right;text-shadow:0 1px 4px rgba(0,0,0,.6)}

/* choose */
.choose{height:232px;background:linear-gradient(180deg,#eef0f2,#fafafa)}
.choose .heading{padding-top:44px;font-size:28px;color:#3a3a3a}
.choose-options{display:flex;justify-content:center;gap:18px;margin-top:36px}
.choose-options .btn{width:258px;text-align:center;padding:16px 0}

/* how */
.how{height:560px}
.how .heading{padding-top:90px;color:#3a3a3a}
.steps{position:absolute;top:183px;left:0;width:1200px;display:flex;justify-content:center}
.step{width:323px;height:273px;text-align:center;padding-top:38px;font-size:15.5px;line-height:1.5;color:#444}
.step.is-featured{border:1px solid #ddd;box-shadow:0 2px 8px rgba(0,0,0,.12)}
.step-icon{position:relative;width:96px;height:96px;border-radius:50%;background:var(--navy);margin:0 auto 22px;display:flex;align-items:center;justify-content:center}
.step-num{position:absolute;right:-8px;top:-4px;width:30px;height:30px;border-radius:50%;background:var(--white);border:2px solid var(--navy);color:var(--navy);font-size:13px;line-height:26px}
.step p{padding:0 28px}

/* pricing */
.pricing{height:720px;background:linear-gradient(180deg,#3a3e45 0%,#25282d 100%)}
.pricing-band{position:absolute;left:0;top:380px;width:1200px;height:340px;background:var(--white)}
.pricing .heading{padding-top:78px;color:var(--white)}
.plans{position:absolute;top:195px;left:82px;display:flex;gap:19px}
.plan{width:191px;height:380px;background:var(--white);box-shadow:0 2px 8px rgba(0,0,0,.25);text-align:center}
.plan-name{height:34px;line-height:34px;font-family:'Oswald',Arial,sans-serif;font-size:17px;color:#222}
.plan-band{height:58px;background:#2d3036;position:relative}
.plan-band.is-custom{color:var(--white);font-family:'Oswald',Arial,sans-serif;font-size:13px;line-height:1.4;padding-top:10px}
.plan-price{position:absolute;left:50%;top:-6px;transform:translateX(-50%);width:78px;height:78px;border-radius:50%;background:var(--orange);border:4px solid var(--white);color:var(--white);font-family:'Oswald',Arial,sans-serif;font-size:24px;line-height:70px}
.plan ol{list-style:none;padding:40px 18px 0;font-size:12.5px;line-height:1.45;color:#444}
.plan li{margin-bottom:10px}
.plan-buy{color:var(--orange);font-family:'Oswald',Arial,sans-serif;font-size:13px;text-transform:uppercase;display:block;margin-top:6px}
.pricing-cta{position:absolute;top:632px;left:0;width:1200px;text-align:center}

/* subscribe */
.gap{height:50px}
.subscribe{height:765px;background:var(--gray)}
.subscribe .heading{padding-top:100px;font-size:34px;line-height:1.5;color:#2c2c2c}
.services{position:absolute;top:280px;left:80px;display:flex}
.service{width:260px;text-align:center}
.service-icon{width:114px;height:114px;border-radius:50%;border:2px solid var(--blue);background:var(--white);margin:0 auto 36px;display:flex;align-items:center;justify-content:center}
.service h3{font-family:'Oswald',Arial,sans-serif;font-weight:500;font-size:19px;margin-bottom:14px;color:#222}
.service p{font-size:15px;line-height:1.55;color:#444;padding:0 20px}
.subscribe-cta{position:absolute;top:638px;left:0;width:1200px;text-align:center}

/* service area */
.area{height:715px}
.area-band{position:absolute;left:0;top:0;width:1200px;height:470px;background:linear-gradient(180deg,#1e3a7d,#102556)}
.area .heading{position:relative;padding-top:60px;color:var(--white)}
.area-search{position:absolute;left:93px;top:145px;width:1014px;height:52px;background:#e9e9e9;display:flex;align-items:center;gap:12px;padding-left:22px;font-size:15px;color:#333;box-shadow:0 2px 6px rgba(0,0,0,.2)}
.area-map{position:absolute;left:93px;top:205px;width:1014px;height:402px;background:linear-gradient(135deg,#cfe1c7 0%,#e8e4da 45%,#a9c9e8 80%);box-shadow:0 2px 10px rgba(0,0,0,.25)}

/* faq */
.faq{height:650px}
.faq .heading{padding-top:40px;color:#2c2c2c}
.faq-list{position:absolute;top:118px;left:173px;width:857px}
.faq-item{height:88px;border:1px solid #ddd;border-left:5px solid var(--orange);box-shadow:0 2px 6px rgba(0,0,0,.1);padding:16px 28px;margin-bottom:16px}
.faq-item h4{font-weight:400;font-size:17px;color:#222;margin-bottom:8px}
.faq-item p{font-size:14px;color:#555}

/* quote */
.quote{height:230px;background:linear-gradient(180deg,#1f3a78,#163066);overflow:visible}
.quote-mark{position:absolute;left:568px;top:-24px;width:64px;height:64px;border-radius:50%;background:var(--white);display:flex;align-items:center;justify-content:center;font-family:'Oswald',Arial,sans-serif;font-size:52px;color:var(--navy);line-height:1;padding-top:18px}
.quote blockquote{position:absolute;top:88px;left:150px;width:900px;text-align:center;color:var(--white);font-size:15px;line-height:1.9}
.quote cite{display:block;margin-top:14px;font-size:13px;color:#c8d2ea}

/* footer */
.site-footer{height:345px;background:#1f2125;color:var(--white)}
.footer-col{position:absolute;top:90px}
.footer-col h5{font-family:'Oswald',Arial,sans-serif;font-weight:400;font-size:21px;text-transform:uppercase;margin-bottom:20px}
.about{left:90px;width:330px;font-size:14.5px;line-height:1.7}
.contact{left:508px;width:260px}
.contact-row{display:flex;gap:12px;margin-bottom:16px;font-size:14px;line-height:1.5}
.contact-row strong{display:block;font-size:15px;text-transform:uppercase}
.form{left:808px;width:306px}
.form-grid{display:grid;grid-template-columns:1fr 1fr;gap:8px}
.field{height:34px;background:var(--white);color:#555;font-size:13px;padding:8px 10px}
.field.wide{grid-column:1/3}
.submit{display:inline-block;margin-top:10px;background:var(--orange);color:var(--white);font-size:13px;padding:6px 20px}
.copyright{height:71px;background:#16181b;color:#aaa;font-size:13px;text-align:center;line-height:71px}
</style>
</head>
<body>

<header class="site-header">
  <div class="brand"><span class="brand-mark"></span><span class="brand-name">Tally Porch Helpers</span></div>
  <div class="top-call">
    <svg width="18" height="18" viewBox="0 0 24 24"><path fill="#f26a1b" d="M6.6 10.8a15 15 0 0 0 6.6 6.6l2.2-2.2c.3-.3.7-.4 1-.2 1.1.4 2.3.6 3.6.6.6 0 1 .4 1 1V20c0 .6-.4 1-1 1C10.6 21 3 13.4 3 4c0-.6.4-1 1-1h3.5c.6 0 1 .4 1 1 0 1.3.2 2.5.6 3.6.1.3 0 .7-.2 1z"/></svg>
    Call Or Text Us 1-555-010-2233
  </div>
  <nav class="main-nav"><span>How it works</span><span>Service</span><span>Pricing</span><span>About us</span><span>Faq</span><span>Contact</span></nav>
</header>

<section class="hero">
  <div class="hero-photo" role="img" aria-label="Suburban house with garden and an open house yard sign on the lawn"></div>
  <p class="hero-copy">Helping agents save time and money. We place signs and boost foot traffic to your open houses using proven marketing techniques.</p>
</section>

<section class="choose">
  <h2 class="heading">Choose the option below that best describes you</h2>
  <div class="choose-options">
    <span class="btn">I'm a full on brokerage</span>
    <span class="btn">I'm an ind. broker with a team</span>
    <span class="btn">I need sign placement asap</span>
  </div>
</section>

<section class="how">
  <h2 class="heading">How it works</h2>
  <div class="steps">
    <div class="step">
      <div class="step-icon"><span class="step-num">1</span>
        <svg width="40" height="48" viewBox="0 0 24 30"><path fill="none" stroke="#fff" stroke-width="2" d="M12 28s9-10 9-17a9 9 0 0 0-18 0c0 7 9 17 9 17z"/><circle cx="12" cy="11" r="3.5" fill="#fff"/></svg></div>
      <p>We Boost Foot Traffic To Your Open House Using Proven Marketing Channels, Social Media Ads, SMS Notifications, Voice Broadcasts and Email Notifications</p>
    </div>
    <div class="step is-featured">
      <div class="step-icon"><span class="step-num">2</span>
        <svg width="48" height="44" viewBox="0 0 30 28"><path fill="none" stroke="#fff" stroke-width="2" d="M3 13 15 3l12 10M6 11v14h18V11"/><rect x="12" y="17" width="6" height="8" fill="#fff"/></svg></div>
      <p>We Place Open House Signs Strategically In The Surrounding Area</p>
    </div>
    <div class="step">
      <div class="step-icon"><span class="step-num">3</span>
        <svg width="48" height="44" viewBox="0 0 30 28"><rect x="4" y="4" width="22" height="13" fill="none" stroke="#fff" stroke-width="2"/><path stroke="#fff" stroke-width="2" d="M9 17v9M21 17v9M8 10h14"/></svg></div>
      <p>We Pick Up The Signs Once Your Open House Ends</p>
    </div>
  </div>
</section>

<section class="pricing">
  <div class="pricing-band"></div>
  <h2 class="heading">Pricing package</h2>
  <div class="plans">
    <div class="plan"><div class="plan-name">5 Signs</div><div class="plan-band"><span class="plan-price">$49</span></div>
      <ol><li>1. Place signs strategically in best areas according to where the open house is located</li><li>2. Pick Up the signs after the open house</li><li>3. Store custom signs for you if needed</li></ol><span class="plan-buy">Buy now »</span></div>
    <div class="plan"><div class="plan-name">10 Signs</div><div class="plan-band"><span class="plan-price">$59</span></div>
      <ol><li>1. Place signs strategically in best areas according to where the open house is located</li><li>2. Pick Up the signs after the open house</li><li>3. Store custom signs for you if needed</li></ol><span class="plan-buy">Buy now »</span></div>
    <div class="plan"><div class="plan-name">15 Signs</div><div class="plan-band"><span class="plan-price">$69</span></div>
      <ol><li>1. Place signs strategically in best areas according to where the open house is located</li><li>2. Pick Up the signs after the open house</li><li>3. Store custom signs for you if needed</li></ol><span class="plan-buy">Buy now »</span></div>
    <div class="plan"><div class="plan-name">20 Signs</div><div class="plan-band"><span class="plan-price">$79</span></div>
      <ol><li>1. Place signs strategically in best areas according to where the open house is located</li><li>2. Pick Up the signs after the open house</li><li>3. Store custom signs for you if needed</li></ol><span class="plan-buy">Buy now »</span></div>
    <div class="plan"><div class="plan-name">25+ Signs</div><div class="plan-band is-custom">Click Buy Now<br>To Create Custom Pkg</div>
      <ol><li>1. Place signs strategically in best areas according to where the open house is located</li><li>2. Pick Up the signs after the open house</li><li>3. Store custom signs for you if needed</li></ol><span class="plan-buy">Buy now »</span></div>
  </div>
  <div class="pricing-cta"><span class="btn">Subscribe to email list</span></div>
</section>

<div class="gap"></div>

<section class="subscribe">
  <h2 class="heading">Sign up for a subscription and get these<br>marketing services for free</h2>
  <div class="services">
    <div class="service"><div class="service-icon"><svg width="44" height="40" viewBox="0 0 24 22"><path fill="none" stroke="#2f6fb5" stroke-width="1.6" d="M2 2h20v13H9l-5 4v-4H2z"/><circle cx="8" cy="8.5" r="1" fill="#2f6fb5"/><circle cx="12" cy="8.5" r="1" fill="#2f6fb5"/><circle cx="16" cy="8.5" r="1" fill="#2f6fb5"/></svg></div>
      <h3>SMS</h3><p>Send sms blast to your neighborhood informing them your home is for sale and if they know anyone looking to send them over</p></div>
    <div class="service"><div class="service-icon"><svg width="48" height="34" viewBox="0 0 24 17"><rect x="1" y="1" width="22" height="15" fill="none" stroke="#2f6fb5" stroke-width="1.6"/><path fill="none" stroke="#2f6fb5" stroke-width="1.6" d="m1 1 11 9 11-9"/></svg></div>
      <h3>EMAIL</h3><p>Email blast to your neighborhood informing them your home is for sale and if they know anyone looking to send them over</p></div>
    <div class="service"><div class="service-icon"><svg width="40" height="40" viewBox="0 0 24 24"><rect x="2" y="2" width="20" height="20" rx="3" fill="none" stroke="#2f6fb5" stroke-width="1.6"/><path fill="none" stroke="#2f6fb5" stroke-width="1.6" d="M7 12h10M7 16h10M7 8h6"/></svg></div>
      <h3>SOCIAL AD</h3><p>Newsfeed ads to people in your open house area</p></div>
    <div class="service"><div class="service-icon"><svg width="40" height="40" viewBox="0 0 24 24"><path fill="none" stroke="#2f6fb5" stroke-width="1.6" d="M13 2h9v9L11 22 2 13z"/><circle cx="17.5" cy="6.5" r="1.5" fill="#2f6fb5"/></svg></div>
      <h3>VB</h3><p>VB blast to your neighborhood informing them your home is for sale and if they know anyone looking to send them over</p></div>
  </div>
  <div class="subscribe-cta"><span class="btn btn-blue">Sign up</span></div>
</section>

<section class="area">
  <div class="area-band"></div>
  <h2 class="heading">Service area</h2>
  <div class="area-search">
    <svg width="14" height="18" viewBox="0 0 24 30"><path fill="#333" d="M12 29S21 18 21 11a9 9 0 0 0-18 0c0 7 9 18 9 18z"/></svg>
    Enter Your Open House Address To See If We Service It
  </div>
  <div class="area-map" role="img" aria-label="Street map of the service region with a location pin"></div>
</section>

<section class="faq">
  <h2 class="heading">FAQ</h2>
  <div class="faq-list">
    <div class="faq-item"><h4>Q- Why choose Porch Helpers ?</h4><p>A- It is a long established fact that a reader will be distracted by the readable content of a page.</p></div>
    <div class="faq-item"><h4>Q- quisquam est qui dolorem ipsum quia dolor sit amet?</h4><p>A- The point of using Lorem Ipsum is that it has a more-or-less normal distribution of letters, as opposed</p></div>
    <div class="faq-item"><h4>Q- Neque porro quisquam est qui dolorem ipsum quia dolor sit amet?</h4><p>A- Lorem Ipsum as their default model text, and a search for 'lorem ipsum' will uncover many web sites.</p></div>
    <div class="faq-item"><h4>Q- Porro quisquam est qui dolorem ipsum quia dolor sit amet, consectetur?</h4><p>A- Various versions have evolved over the years, sometimes by accident, sometimes on purpose</p></div>
  </div>
</section>

<section class="quote">
  <div class="quote-mark">“</div>
  <blockquote>The point of using Lorem Ipsum is that it has a more-or-less normal distribution of letters, as opposed to using 'Content here, content here', making it look like readable English.Many desktop publishing packages and web page editors now
    <cite>- Neque porro quisquam</cite></blockquote>
</section>

<footer class="site-footer">
  <div class="footer-col about"><h5>About us</h5><p>Owned and operated by a Highly Experienced and Skilled Promoter, An Expert Marketer and a Savvy Realtor, we help agents leverage their time and skills to increase production at an affordable price with impeccable support!</p></div>
  <div class="footer-col contact"><h5>Contact us</h5>
    <div class="contact-row"><svg width="18" height="22" viewBox="0 0 24 30"><path fill="none" stroke="#fff" stroke-width="2" d="M12 28s9-10 9-17a9 9 0 0 0-18 0c0 7 9 17 9 17z"/><circle cx="12" cy="11" r="3" fill="#fff"/></svg><div><strong>Address</strong>48 Birchwood Lane, Suite B<br>Harlow, NC 27000</div></div>
    <div class="contact-row"><svg width="18" height="18" viewBox="0 0 24 24"><path fill="#fff" d="M6.6 10.8a15 15 0 0 0 6.6 6.6l2.2-2.2c.3-.3.7-.4 1-.2 1.1.4 2.3.6 3.6.6.6 0 1 .4 1 1V20c0 .6-.4 1-1 1C10.6 21 3 13.4 3 4c0-.6.4-1 1-1h3.5c.6 0 1 .4 1 1 0 1.3.2 2.5.6 3.6.1.3 0 .7-.2 1z"/></svg><div><strong>Phone number</strong>1-555-010-2233</div></div>
  </div>
  <div class="footer-col form"><h5>Contact form</h5>
    <div class="form-grid"><span class="field">Name</span><span class="field">Cell Phone</span><span class="field wide">Email</span><span class="field wide">Message</span></div>
    <span class="submit">Submit</span>
  </div>
</footer>
<div class="copyright">© 2018 Company Name . All right reserved</div>

</body>
</html>
```